Kelvaro.ch is looking for business card letterhead and envelope C5 with WOW effect

We need a strong business card for our company Kelvaro.ch, logo is available. You want a black or dark background on which the logo Stark r% 26 # 252; appears. Letterhead and envelope in C5 format should be in a similar design, but does not have to be We need a strong business card for our company Kelvaro.ch, logo is available. A black or dark background is desired, on which the logo Stark comes across. The letterhead and the envelope in C5 format should have a similar design.

Target Market(s)

Private customers as well as entrepreneurs

Contact Information for Business Card

E-mail: info@kelvaro-example.ch
Web.www.Kelvaro-example.ch
Tel: +41 ( 0 ) 79 482 6037
Adresse:
Lindenweg 14
9406 Tarnbach

Hier kann man Icons verwenden für Email,Tel und Adressse

Font styles to use
Other font styles liked:
• Dubai,bold

Colors

Designer to choose colors to be used in the design.

Requirements
Must have
• WOW effect
Nice to have
• R% 26 # 252; back business card with our service listings. - VEHICLE LABELING - SHOP WINDOW LABELING - STICKERS AND MUCH MORE ... in red color

```html
<!DOCTYPE html>
<html lang="en">
<head>
<meta charset="utf-8">
<title>Kelvaro.ch – Business Card</title>
<link href="https://fonts.googleapis.com/css2?family=Arimo:wght@400&family=Saira+Semi+Condensed:wght@500;700&display=swap" rel="stylesheet">
<style>
  :root {
    --page-bg: #d9d9d9;
    --card-black: #0a0a0a;
    --brand-yellow: #fdc91f;
    --text-white: #ffffff;
    --service-red: #e8141b;
  }
  * { margin: 0; padding: 0; box-sizing: border-box; }
  html, body { width: 1200px; height: 802px; overflow: hidden; }
  body { background: var(--page-bg); position: relative; }

  .card {
    position: absolute;
    top: 274px;
    width: 442px;
    height: 265px;
    overflow: hidden;
    box-shadow: 0 3px 8px rgba(0,0,0,0.35);
  }
  .card--front { left: 136px; background: var(--card-black); }
  .card--back { left: 624px; background: var(--brand-yellow); }

  .brand-name {
    position: absolute;
    z-index: 2;
    font-family: "Saira Semi Condensed", sans-serif;
    font-weight: 700;
    font-size: 26px;
    letter-spacing: 0.3px;
    line-height: 1;
    white-space: nowrap;
  }
  .card--front .brand-name { left: 24px; top: 46px; color: var(--text-white); }

  .contact-list { position: absolute; z-index: 2; left: 24px; top: 140px; list-style: none; }
  .contact-item {
    display: flex; align-items: center; gap: 6px;
    height: 18px;
    font-family: "Arimo", sans-serif;
    font-size: 12.5px;
    color: var(--text-white);
    white-space: nowrap;
  }
  .contact-icon { width: 15px; height: 15px; flex: none; }

  .address {
    position: absolute; z-index: 2; left: 26px; top: 214px;
    font-family: "Arimo", sans-serif;
    font-size: 12.5px;
    color: var(--text-white);
    white-space: nowrap;
  }

  .honeycomb-area {
    position: absolute; z-index: 1; right: 0; top: 0;
    width: 196px; height: 100%;
    background: linear-gradient(90deg, var(--card-black) 0%, #6b5411 30%, var(--brand-yellow) 70%, #b58f14 100%);
  }

  .card--back .brand-mark {
    position: absolute; left: 146px; top: 91px;
    width: 22px; height: 22px;
    background: var(--card-black);
  }
  .card--back .brand-name { left: 178px; top: 89px; color: var(--card-black); }

  .service-band {
    position: absolute; left: 0; bottom: 0;
    width: 100%; height: 57px;
    background: var(--card-black);
    display: flex; flex-direction: column; justify-content: center; align-items: center;
    font-family: "Saira Semi Condensed", sans-serif;
    font-weight: 500;
    font-size: 11.5px;
    line-height: 14px;
    color: var(--service-red);
    text-transform: uppercase;
    white-space: nowrap;
  }
</style>
</head>
<body>

<section class="card card--front">
  <div class="brand-name">KELVARO.CH</div>

  <ul class="contact-list">
    <li class="contact-item">
      <svg class="contact-icon" viewBox="0 0 16 16" aria-hidden="true">
        <rect x="1" y="1" width="14" height="14" rx="2" fill="none" stroke="#fdc91f" stroke-width="1.5"/>
        <path d="M5 4 l2 0 l0.8 2.3 l-1.2 1 a6 6 0 0 0 2.2 2.2 l1-1.2 l2.3 0.8 l0 2 a1 1 0 0 1-1 1 a7.5 7.5 0 0 1-7-7 a1 1 0 0 1 1-1z" fill="#fdc91f"/>
      </svg>
      <span>+41 ( 0 ) 79 482 6037</span>
    </li>
    <li class="contact-item">
      <svg class="contact-icon" viewBox="0 0 16 16" aria-hidden="true">
        <rect x="0.5" y="3" width="15" height="10" fill="#fdc91f"/>
        <path d="M0.5 3 L8 9 L15.5 3 M0.5 13 L6 8 M15.5 13 L10 8" fill="none" stroke="#0a0a0a" stroke-width="1.2"/>
      </svg>
      <span>info@kelvaro-example.ch</span>
    </li>
    <li class="contact-item">
      <svg class="contact-icon" viewBox="0 0 16 16" aria-hidden="true">
        <g fill="none" stroke="#fdc91f" stroke-width="1.4">
          <circle cx="8" cy="8" r="6.8"/>
          <ellipse cx="8" cy="8" rx="3" ry="6.8"/>
          <path d="M1.2 8 H14.8 M2.5 4.5 H13.5 M2.5 11.5 H13.5"/>
        </g>
      </svg>
      <span>www.Kelvaro-example.ch</span>
    </li>
  </ul>

  <p class="address">Lindenweg 14, 9406 Tarnbach</p>

  <div class="honeycomb-area" role="img" aria-label="Yellow and black honeycomb hexagon pattern"></div>
</section>

<section class="card card--back">
  <span class="brand-mark" aria-hidden="true"></span>
  <div class="brand-name">KELVARO.CH</div>

  <div class="service-band">
    <span>Vehicle labeling | Shop window labeling</span>
    <span>Stickers and much more ...</span>
  </div>
</section>

</body>
</html>
```